Need help in designing new business card utilizing our new logo.

BuildMark Solutions works with Construction Business Owners, Managers & IT Professionals to strengthen software usage and increase user productivity.

Our Construction Accounting and Mobile Field Management Software Clients engage with us in the following areas:

New Software Implementations
Software Re-Implementations
Redesigning Software Usage at the User Level
Project Coordination & Management
Continued Software Support

Old tag line:
Weighing Options - Implementing Solutions

www.buildmark-solutions.example

Ridge 4 is a product, but not needed for a new business card.

```html
<!DOCTYPE html>
<html lang="en">
<head>
<meta charset="utf-8">
<title>BuildMark Solutions – Business Card</title>
<link rel="stylesheet" href="https://fonts.googleapis.com/css2?family=Roboto:wght@400;500;700&display=swap">
<style>
  :root {
    --stage: #3a3a3c;
    --card: #232427;
    --blue: #0d4a9a;
    --blue-bright: #1457b8;
    --white: #ffffff;
    --silver: #b9bbbf;
    --muted: #d8d8d8;
  }
  * { margin: 0; padding: 0; box-sizing: border-box; }
  html, body { width: 799px; height: 1200px; overflow: hidden; }
  body {
    background: var(--stage);
    font-family: "Roboto", Arial, sans-serif;
    color: var(--white);
    position: relative;
  }
  .card {
    position: absolute;
    left: 89px;
    width: 620px;
    height: 354px;
    background: var(--card);
    border-radius: 22px;
    overflow: hidden;
  }
  .card--front { top: 130px; }
  .card--back { top: 716px; }

  /* Front */
  .front-brand {
    position: absolute;
    top: 62px; left: 0; right: 0;
    display: flex; justify-content: center; align-items: center; gap: 14px;
  }
  .brand-square { width: 18px; height: 18px; background: var(--silver); }
  .front-brand .brand-name {
    font-weight: 700; font-size: 36px; color: var(--silver); letter-spacing: 1px;
  }
  .service-band {
    position: absolute;
    top: 152px; left: 0; right: 0; height: 116px;
    background: var(--blue);
    display: flex; flex-direction: column; justify-content: center; align-items: center;
    gap: 6px;
    font-size: 17px; line-height: 1.15;
  }
  .service-band .divider { padding: 0 8px; }
  .front-web {
    position: absolute;
    top: 290px; left: 0; right: 0;
    display: flex; justify-content: center; align-items: center; gap: 22px;
    font-size: 15px;
  }
  .front-web .rule { width: 44px; height: 2px; background: var(--muted); }

  /* Back */
  .name-arc {
    position: absolute; top: 26px; left: -70px;
    width: 86px; height: 86px; border-radius: 50%;
    background: var(--blue-bright);
  }
  .identity { position: absolute; top: 34px; left: 34px; }
  .identity .person {
    font-weight: 700; font-size: 22px; color: var(--blue-bright);
  }
  .identity .role { font-size: 11px; margin-top: 2px; }
  .address {
    position: absolute; top: 140px; left: 34px;
    font-size: 14px; line-height: 1.3;
  }
  .contacts {
    position: absolute; top: 194px; left: 34px;
    list-style: none; font-size: 14px;
  }
  .contacts li { display: flex; align-items: center; gap: 10px; height: 21px; }
  .contacts svg { width: 13px; height: 13px; fill: var(--blue-bright); flex: none; }
  .back-brand {
    position: absolute; right: 34px; bottom: 40px;
    display: flex; align-items: center; gap: 12px;
  }
  .back-brand .brand-square { background: var(--blue-bright); }
  .back-brand .brand-name {
    font-weight: 700; font-size: 30px; color: var(--blue-bright);
  }
</style>
</head>
<body>
  <section class="card card--front">
    <div class="front-brand">
      <span class="brand-square"></span>
      <span class="brand-name">BuildMark Solutions</span>
    </div>
    <div class="service-band">
      <p>New Software Implementations<span class="divider">|</span>Software Re-Implementations</p>
      <p>Redesigning Software Usage at the User Level</p>
      <p>Project Coordination &amp; Management<span class="divider">|</span>Continued Software Support</p>
    </div>
    <div class="front-web">
      <span class="rule"></span>
      <span>www.buildmark-solutions.example</span>
      <span class="rule"></span>
    </div>
  </section>

  <section class="card card--back">
    <span class="name-arc"></span>
    <div class="identity">
      <p class="person">Dana R. Whitfield</p>
      <p class="role">Owner</p>
    </div>
    <p class="address">14B Harbor Lane - Suite 210<br>Lakeview, NY 12000</p>
    <ul class="contacts">
      <li>
        <svg viewBox="0 0 16 16" aria-hidden="true"><rect x="4" y="1" width="8" height="14" rx="1.5"/><rect x="5.5" y="3" width="5" height="8" fill="#232427"/></svg>
        555-014-2281
      </li>
      <li>
        <svg viewBox="0 0 16 16" aria-hidden="true"><path d="M3 1h3l1.5 4-2 1.5a9 9 0 0 0 4 4l1.5-2 4 1.5v3a1 1 0 0 1-1 1A13 13 0 0 1 2 2a1 1 0 0 1 1-1z"/></svg>
        555-019-4470 ext. 100
      </li>
      <li>
        <svg viewBox="0 0 16 16" aria-hidden="true"><rect x="1" y="3" width="14" height="10" rx="1"/><path d="M1.5 3.5 8 9l6.5-5.5" stroke="#232427" stroke-width="1.4" fill="none"/></svg>
        dana.whitfield@buildmark-solutions.example
      </li>
      <li>
        <svg viewBox="0 0 16 16" aria-hidden="true"><circle cx="8" cy="8" r="7"/><path d="M1 8h14M8 1c-3 3-3 11 0 14M8 1c3 3 3 11 0 14" stroke="#232427" stroke-width="1.1" fill="none"/></svg>
        www.buildmark-solutions.example
      </li>
    </ul>
    <div class="back-brand">
      <span class="brand-square"></span>
      <span class="brand-name">BuildMark Solutions</span>
    </div>
  </section>
</body>
</html>
```